Brookvane Consulting Business Card Design

Business Card Design for Brookvane Consulting. Brookvane Consulting is a boutique consultancy based in Atlanta, GA., that specializes in marketing strategy, organization planning, and leadership development. We provide solutions for small businesses and startups as well as Vantage 300 companies.

http://brookvaneconsulting.com/

Target Market(s)

We provide solutions for small businesses and startups as well as Vantage 300 companies.

Industry/Entity Type

Consulting

Contact Information for Business Card

Two sided business card with priority on contact information, logo, tag line (Guidance to Think Bigger, Act Bolder, Grow Further)

Colors

Designer to choose colors to be used in the design.

Requirements
Must have
• contact information, logo, tag line (Guidance to Think Bigger, Act Bolder, Grow Further)
• Simple no over communication.
Nice to have
• I would like to see different placements of logo and creative use of both sides of the card
Should not have
• Do not put too much information on the card.

```html
<!DOCTYPE html>
<html lang="en">
<head>
<meta charset="utf-8">
<title>Brookvane Consulting Business Card</title>
<link href="https://fonts.googleapis.com/css2?family=Lato:wght@400;700&display=swap" rel="stylesheet">
<style>
  :root {
    --backdrop: #3a332e;
    --card: #141414;
    --card-edge: #1c1c1c;
    --ink-light: #ffffff;
    --ink-muted: #b9b9b9;
    --ink-soft: #8d8d8d;
    --band: #ffffff;
    --band-ink: #111111;
  }
  * { margin: 0; padding: 0; box-sizing: border-box; }
  html, body {
    width: 1200px; height: 769px; overflow: hidden;
    background: var(--backdrop);
    font-family: "Lato", sans-serif;
  }
  .stage {
    position: relative; width: 1200px; height: 769px;
    display: flex; align-items: center; justify-content: center; gap: 50px;
  }
  .card {
    position: relative; width: 525px; height: 300px;
    background: var(--card);
    border: 1px solid var(--card-edge);
    border-radius: 4px;
    overflow: hidden;
    box-shadow: 0 14px 30px rgba(0,0,0,0.45);
  }
  .wordmark {
    position: absolute;
    display: flex; align-items: center; gap: 10px;
    color: var(--ink-light);
    font-weight: 700;
    line-height: 1.05;
  }
  .wordmark-dot {
    width: 12px; height: 12px; border-radius: 50%;
    background: var(--ink-light); flex: none;
  }
  .wordmark-name { display: block; }

  /* Contact side */
  .card-contact .wordmark { left: 40px; top: 88px; font-size: 30px; }
  .identity {
    position: absolute; right: 40px; top: 80px; text-align: right;
  }
  .identity-name {
    color: var(--ink-soft); font-weight: 700; font-size: 17px; letter-spacing: 0.5px;
  }
  .identity-title {
    color: var(--ink-muted); font-size: 14px; margin-top: 4px;
  }
  .contact-list {
    position: absolute; left: 40px; bottom: 36px; list-style: none;
  }
  .contact-list li {
    display: flex; align-items: center; gap: 10px;
    color: var(--ink-muted); font-size: 14px; line-height: 22px;
  }
  .contact-list svg { width: 13px; height: 13px; flex: none; fill: var(--ink-muted); }

  /* Tagline side */
  .card-brand .wordmark {
    left: 0; right: 0; top: 82px; justify-content: center; font-size: 40px;
  }
  .tagline-band {
    position: absolute; left: 0; right: 0; bottom: 58px; height: 40px;
    background: var(--band);
    display: flex; align-items: center; justify-content: flex-end;
    padding-right: 34px;
  }
  .tagline {
    color: var(--band-ink); font-size: 13px; font-weight: 700;
  }
</style>
</head>
<body>
<main class="stage">
  <section class="card card-contact" aria-label="Card contact side">
    <div class="wordmark">
      <span class="wordmark-dot"></span>
      <span class="wordmark-name">Brookvane<br>Consulting</span>
    </div>
    <div class="identity">
      <p class="identity-name">DARREN WHITFIELD</p>
      <p class="identity-title">Founder/Managing Director</p>
    </div>
    <ul class="contact-list">
      <li>
        <svg viewBox="0 0 24 24" aria-hidden="true"><path d="M6.6 10.8a15.1 15.1 0 0 0 6.6 6.6l2.2-2.2a1 1 0 0 1 1-.25 11.4 11.4 0 0 0 3.6.57 1 1 0 0 1 1 1V20a1 1 0 0 1-1 1A17 17 0 0 1 3 4a1 1 0 0 1 1-1h3.5a1 1 0 0 1 1 1c0 1.25.2 2.45.57 3.6a1 1 0 0 1-.25 1z"/></svg>
        555-214-3090
      </li>
      <li>
        <svg viewBox="0 0 24 24" aria-hidden="true"><path d="M2 5h20v14H2z M3.5 6.5 12 13l8.5-6.5" fill="none" stroke="#b9b9b9" stroke-width="2"/></svg>
        darren@brookvaneconsulting.com
      </li>
      <li>
        <svg viewBox="0 0 24 24" aria-hidden="true"><circle cx="12" cy="12" r="9.5" fill="none" stroke="#b9b9b9" stroke-width="2"/><path d="M2.5 12h19M12 2.5c3 3 3 16 0 19M12 2.5c-3 3-3 16 0 19" fill="none" stroke="#b9b9b9" stroke-width="1.6"/></svg>
        brookvaneconsulting.com
      </li>
    </ul>
  </section>

  <section class="card card-brand" aria-label="Card brand side">
    <div class="wordmark">
      <span class="wordmark-dot"></span>
      <span class="wordmark-name">Brookvane Consulting</span>
    </div>
    <div class="tagline-band">
      <p class="tagline">Guidance to Think Bigger, Act Bolder, Grow Further</p>
    </div>
  </section>
</main>
</body>
</html>
```